Letterhead Design Project

I would like some modern, youthful, yet professional.

Industry/Entity Type

It Professional

Requirements
Must have
• On the left side the names of the Planning Committee:
Planning Committee
Founding Leaders:
Dorvena Pike, RISE Youngsters - Washington, DC
Marisol Trevane, RISE Youngsters - Washington, DC
Benedira Coltrop, RISE Youngsters - Washington, DC
Gregory Ashfield, RISE Youngsters - Washington, DC
Wren Talbek, Alliance of Northern Prairie Young People Support Circle
Petra Vondrakova, Alliance of Northern Prairie Young People Support Circle
Rosalind Burke, Countrywide Young People Support Circle, Canada
Irit Glen Shoval, Countrywide Young People Support Circle, Canada
Chair
Kendra Oduya, RISE Youngsters, Washington, DC
Co-Chairs
Ruth Palmquist, Global Guardian Homes Association, Amsterdam. Netherlands
Tessa Whitlow, Bright Pathway Partners, Jackson, MS
Owen Strade, Martha J Peller Trust

```html
<!DOCTYPE html>
<html lang="en">
<head>
<meta charset="utf-8">
<title>Letterhead – Planning Committee</title>
<link href="https://fonts.googleapis.com/css2?family=Questrial&display=swap" rel="stylesheet">
<style>
  :root {
    --band-light: #6cc3ec;
    --band-mid: #2e9fd9;
    --band-deep: #1783c4;
    --text-on-band: #ffffff;
    --text-soft: rgba(255, 255, 255, 0.78);
    --brand-blue: #2a8fcc;
    --brand-tint: #d5ecf8;
    --paper: #ffffff;
  }
  html, body {
    margin: 0;
    padding: 0;
    overflow: hidden;
    background: var(--paper);
  }
  .letterhead {
    position: relative;
    width: 900px;
    height: 1200px;
    overflow: hidden;
    background: var(--paper);
    font-family: "Questrial", "Century Gothic", sans-serif;
  }
  .header-band {
    position: absolute;
    top: 0;
    left: 0;
    width: 900px;
    height: 360px;
  }
  .committee {
    position: absolute;
    top: 16px;
    color: var(--text-soft);
    font-size: 10.5px;
    line-height: 15px;
    margin: 0;
    padding: 0;
    list-style: none;
  }
  .committee--founders { left: 36px; }
  .committee--chairs { left: 324px; }
  .committee .role { color: var(--text-on-band); }
  .committee .name { color: var(--text-on-band); }
  .brand {
    position: absolute;
    top: 28px;
    left: 690px;
    width: 180px;
    text-align: center;
    color: var(--brand-blue);
  }
  .brand-mark {
    display: block;
    width: 70px;
    height: 70px;
    margin: 0 auto 12px;
    border-radius: 50%;
    background: var(--brand-tint);
  }
  .brand-name {
    margin: 0;
    font-size: 15px;
    line-height: 18px;
    letter-spacing: 0.3px;
  }
</style>
</head>
<body>
<div class="letterhead">
  <svg class="header-band" viewBox="0 0 900 360" aria-hidden="true">
    <defs>
      <linearGradient id="bandFill" x1="1" y1="0" x2="0" y2="1">
        <stop offset="0" stop-color="var(--band-light)"/>
        <stop offset="0.45" stop-color="var(--band-mid)"/>
        <stop offset="1" stop-color="var(--band-deep)"/>
      </linearGradient>
    </defs>
    <path d="M0 0 H700 C692 88 664 138 604 164 C420 240 210 300 0 352 Z" fill="url(#bandFill)"/>
  </svg>

  <ul class="committee committee--founders">
    <li class="role">Planning Committee</li>
    <li class="role">Founding Leaders:</li>
    <li><span class="name">Dorvena Pike,</span> RISE Youngsters - Washington, DC</li>
    <li><span class="name">Marisol Trevane,</span> RISE Youngsters - Washington, DC</li>
    <li><span class="name">Benedira Coltrop,</span> RISE Youngsters - Washington, DC</li>
    <li><span class="name">Gregory Ashfield,</span> RISE Youngsters - Washington, DC</li>
    <li><span class="name">Wren Talbek,</span> Alliance of Northern Prairie Young People Support Circle</li>
    <li><span class="name">Petra Vondrakova,</span> Alliance of Northern Prairie Young People Support Circle</li>
    <li><span class="name">Rosalind Burke,</span> Countrywide Young People Support Circle, Canada</li>
    <li><span class="name">Irit Glen Shoval,</span> Countrywide Young People Support Circle, Canada</li>
  </ul>

  <ul class="committee committee--chairs">
    <li class="role">Chair</li>
    <li><span class="name">Kendra Oduya,</span> RISE Youngsters, Washington, DC</li>
    <li class="role">Co-Chairs</li>
    <li><span class="name">Ruth Palmquist,</span> Global Guardian Homes Association, Amsterdam. Netherlands</li>
    <li><span class="name">Tessa Whitlow,</span> Bright Pathway Partners, Jackson, MS</li>
    <li><span class="name">Owen Strade,</span> Martha J Peller Trust</li>
  </ul>

  <div class="brand">
    <span class="brand-mark" aria-hidden="true"></span>
    <p class="brand-name">2012 Worldwide Forum<br>of Young People in Care</p>
  </div>
</div>
</body>
</html>
```